BRISKEL Need a luxury modern business card designed.

Need a luxury modern business card designed. refer to the uploaded files for the company name and logo in the zip file under source files. i will making my descion on monday. so please send in before then so if we need to edit we will have the time. we have a trade show coming up and im on a deadline for printer.

Target Market(s)

high end clients

Contact Information for Business Card

Company nAme and logo. Tobias Fennick Co-Founder / Project Manager Office # 555-318-7094 Cell # 555-642-1586 BRISKEL.CA Tobias@briskel-example.ca

Font styles to use
Other font styles liked:
• Modern

Requirements
Must have
• Company name and logo, contact info, using the black, gold and white color scheme.

```html
<!DOCTYPE html>
<html lang="en">
<head>
<meta charset="utf-8">
<title>BRISKEL – Business Card</title>
<link href="https://fonts.googleapis.com/css2?family=Poppins:wght@300;400;500&display=swap" rel="stylesheet">
<style>
  :root {
    --stage: #1c1c1d;
    --card-dark: #2f2f30;
    --ink: #2b2b2c;
    --ink-soft: #6a6a6c;
    --gold: #a8995f;
    --paper: #ffffff;
    --paper-shade: #ececec;
    --rule: #8a8a8a;
  }
  * { box-sizing: border-box; margin: 0; padding: 0; }
  html, body {
    width: 1200px; height: 900px; overflow: hidden;
    background: var(--stage);
    font-family: "Poppins", sans-serif;
  }
  .canvas {
    width: 1200px; height: 900px;
    display: flex; flex-direction: column; align-items: center; justify-content: center;
    gap: 40px;
  }
  .card {
    width: 700px; height: 400px; position: relative; overflow: hidden;
    box-shadow: 0 14px 30px rgba(0,0,0,.55);
  }

  /* Front */
  .card-front {
    background: linear-gradient(150deg, var(--paper) 45%, var(--paper-shade) 100%);
    padding: 56px 0 0 64px;
  }
  .wordmark {
    font-weight: 300; letter-spacing: .32em; line-height: 1;
  }
  .card-front .wordmark { font-size: 42px; color: var(--ink); }
  .tagline {
    font-size: 10px; letter-spacing: .5em; text-transform: uppercase;
    margin-top: 12px; padding-top: 8px;
    border-top: 1px solid var(--rule); width: 330px;
  }
  .card-front .tagline { color: var(--ink-soft); }
  .person { margin-top: 34px; }
  .person-name {
    font-size: 28px; font-weight: 400; letter-spacing: .03em; text-transform: uppercase;
    color: var(--ink); line-height: 1.1;
  }
  .person-name .surname { color: var(--gold); }
  .person-role {
    font-size: 13px; font-weight: 300; text-transform: uppercase; color: var(--ink-soft);
    margin-top: 4px;
  }
  .contact-list { list-style: none; margin-top: 22px; }
  .contact-item {
    display: flex; align-items: center; gap: 12px;
    font-size: 16px; color: var(--ink); line-height: 28px;
  }
  .contact-icon { width: 16px; height: 16px; fill: var(--gold); flex: none; }

  /* Back */
  .card-back {
    background: var(--card-dark);
    display: flex; flex-direction: column; align-items: center; justify-content: center;
  }
  .card-back .wordmark { font-size: 50px; color: var(--paper); padding-left: .32em; }
  .card-back .tagline {
    color: #bdbdbd; text-align: center; width: 380px; margin-top: 14px;
    border-top-color: #6e6e6e; padding-left: .5em;
  }
</style>
</head>
<body>
<main class="canvas">
  <section class="card card-front" aria-label="Business card front">
    <div class="wordmark">BRISKEL</div>
    <div class="tagline">Luxury Landscapes</div>
    <div class="person">
      <h1 class="person-name">Tobias <span class="surname">Fennick</span></h1>
      <p class="person-role">Co-Founder / Project Manager</p>
    </div>
    <ul class="contact-list">
      <li class="contact-item">
        <svg class="contact-icon" viewBox="0 0 16 16" aria-hidden="true"><path d="M3.2 1.2l2.3 2.6-1.3 1.6c.9 2 2.4 3.5 4.4 4.4l1.6-1.3 2.6 2.3-1.1 2.6C6.8 13.6 2.4 9.2 1.2 4.3z"/></svg>
        555 318 7094
      </li>
      <li class="contact-item">
        <svg class="contact-icon" viewBox="0 0 16 16" aria-hidden="true"><path d="M4 1h8v14H4zM5.5 3v8h5V3zM7 12.5h2v1H7z" fill-rule="evenodd"/></svg>
        555 642 1586
      </li>
      <li class="contact-item">
        <svg class="contact-icon" viewBox="0 0 16 16" aria-hidden="true"><path d="M1 3h14v10H1zM2 4l6 5 6-5"/><path d="M1 3h14L8 8.5z" fill="#fff" opacity=".35"/></svg>
        Tobias@briskel-example.ca
      </li>
      <li class="contact-item">
        <svg class="contact-icon" viewBox="0 0 16 16" aria-hidden="true"><path d="M8 1a7 7 0 1 0 0 14A7 7 0 0 0 8 1zm0 1.3c.9 1 1.5 2.6 1.6 4.4H6.4C6.5 4.9 7.1 3.3 8 2.3zM5.1 6.7H2.4a5.7 5.7 0 0 1 3.5-4.2c-.5 1.1-.8 2.6-.8 4.2zm0 1.3c.1 1.6.3 3.1.8 4.2A5.7 5.7 0 0 1 2.4 8zm1.3 0h3.2c-.1 1.8-.7 3.4-1.6 4.4-.9-1-1.5-2.6-1.6-4.4zm4.5 0h2.7a5.7 5.7 0 0 1-3.5 4.2c.5-1.1.8-2.6.8-4.2zm0-1.3c0-1.6-.3-3.1-.8-4.2a5.7 5.7 0 0 1 3.5 4.2z"/></svg>
        briskel.ca
      </li>
    </ul>
  </section>

  <section class="card card-back" aria-label="Business card back">
    <div class="wordmark">BRISKEL</div>
    <div class="tagline">Luxury Landscapes</div>
  </section>
</main>
</body>
</html>
```